Luxury Real Estate Website, Midwest, United States

We need web design services for a luxury website. We need IDX Integration with our MLS. We want this to be a very simple website with amazing graphics. We want it to link up with our MailChimp account in order to generate leads through a "More Information" Pop up on the main page. We want the main page to be covered with one large graphic that is a rolling slideshow of active listings of $400,000 and up from the IDX Integration. We need this website to give a very exclusive and sleek look. Lots of black is good... I will upload our logos in Black and Silver. We will also need an "About" page that we are going to call "Qeno Info". We want our graphics to be extremely impressive. Keep in mind, we are a company in the Midwest of the United States, and our real estate has a different look than homes in California or Florida. We need graphics that are realistic for the Midwest, yet still high-end.
Target Market(s)
Luxury Homeowners in the Midwest United States. The graphics needs to be pristine.
Industry/Entity Type
Real Estate
Coding
Coded - Design and coding required
Number of Pages Required
3 page
Requirements
Must have
- Large graphics with IDX Integration. The photos of real estate need to represent real estate that is common in the Midwest, United States. We also need MailChimp integration. We need a pop up that is titled "My Free Market Analysis" that makes them fill out a contact form asking for Full Name, Email Address, Phone Number and Address. This needs to be a pop up on the front page and will integrate with our MailChimp account. We also need a page called "About Qe No Home". And another page where clients can download informational PDFs. The main component needs to be a front page search engine connected with the IDX to access active listings from our MLS. I attached our logos and a sample front page of a website. I would love for ours to look similar.
Nice to have
- Lake House photos on midwest lakes are a plus.
Should not have
- Should not have clutter. This website needs to be clean, luxurious and exclusive.

```html
<!DOCTYPE html>
<html lang="en">
<head>
<meta charset="utf-8">
<title>Harborline Realty Group — Find Your New Home</title>
<link href="https://fonts.googleapis.com/css2?family=Josefin+Sans:wght@400;600;700&family=Open+Sans:wght@400;600;700&display=swap" rel="stylesheet">
<style>
:root{
  --ink:#1f1f1f;
  --text:#555a60;
  --muted:#8a9097;
  --line:#cfd6df;
  --frame:#b9cbe3;
  --num:#c5d4e8;
  --white:#ffffff;
  --panel:#f4f6f9;
  --tab:#e4e7eb;
  --tab-active:#c9d6e6;
  --dark:#111214;
  --footer:#1c2026;
  --gold:#e9b64a;
  --green:#3a9b4a;
  --blue:#1f5fae;
}
*{box-sizing:border-box;margin:0;padding:0}
html,body{width:1200px;height:3797px;overflow:hidden}
body{position:relative;background:var(--white);font-family:"Open Sans",sans-serif;color:var(--text)}
.abs{position:absolute}
.photo{position:absolute;display:block}
h2.section-title{position:absolute;font-family:"Josefin Sans",sans-serif;font-weight:600;font-size:31px;letter-spacing:1.5px;color:var(--ink);text-transform:uppercase;display:flex;align-items:center;gap:12px}
.num{font-family:"Josefin Sans",sans-serif;font-size:62px;font-weight:400;color:var(--num);line-height:1;position:relative}
.num::before{content:"";position:absolute;left:-10px;top:-6px;width:70px;height:70px;border-radius:50%;background:rgba(197,212,232,.35);z-index:-1}
p.body{font-size:13px;line-height:24px;color:var(--text)}
.btn-outline{position:absolute;border:2px solid var(--ink);font-family:"Open Sans",sans-serif;font-weight:700;font-size:13px;color:var(--ink);display:flex;align-items:center;justify-content:center;gap:6px;text-transform:uppercase;background:var(--white)}
.btn-outline .dot{width:13px;height:13px;border-radius:50%;background:var(--ink);display:inline-flex;align-items:center;justify-content:center}

/* header */
.site-header{position:absolute;left:0;top:0;width:1200px;height:95px;background:var(--white)}
.brand{position:absolute;left:96px;top:28px;display:flex;align-items:center;gap:10px;font-family:"Josefin Sans",sans-serif;font-weight:600;color:var(--ink);font-size:22px;letter-spacing:2px}
.brand .mark{width:16px;height:16px;background:var(--ink)}
.main-nav{position:absolute;right:95px;top:40px;display:flex;gap:30px;font-size:13px;font-weight:600;color:var(--ink);text-transform:uppercase}

/* hero */
.hero{position:absolute;left:0;top:95px;width:1200px;height:557px;background:linear-gradient(180deg,#6f9cc6 0%,#8fb5d2 25%,#7f8f5a 48%,#5a6b45 62%,#3f5a5e 80%,#4b5a40 100%)}
.hero h1{position:absolute;left:0;width:1200px;top:210px;text-align:center;font-family:"Josefin Sans",sans-serif;font-weight:700;font-size:52px;color:var(--white);letter-spacing:1px;text-shadow:0 2px 6px rgba(0,0,0,.4)}
.search-tab{position:absolute;left:210px;top:298px;width:168px;height:40px;background:#2c2f33;color:var(--white);font-size:16px;font-weight:600;display:flex;align-items:center;justify-content:center;text-transform:uppercase}
.search-bar{position:absolute;left:210px;top:338px;width:778px;height:60px;background:rgba(30,32,36,.85);padding:10px 13px}
.search-bar .field{width:100%;height:40px;background:var(--white);display:flex;align-items:center;font-size:12px;color:var(--muted);padding-left:14px;position:relative}
.search-bar .go{position:absolute;right:0;top:0;width:62px;height:40px;background:#c8ced6;display:flex;align-items:center;justify-content:center}
.slide-arrow{position:absolute;width:34px;height:34px;border-radius:50%;background:rgba(20,20,20,.75);display:flex;align-items:center;justify-content:center}

/* sections */
.properties{position:absolute;left:0;top:652px;width:1200px;height:838px;background:linear-gradient(180deg,#ffffff 0%,#f6f8fb 100%)}
.about{position:absolute;left:0;top:1490px;width:1200px;height:495px;background:linear-gradient(180deg,#eef1f5,#e8ecf1)}
.featured{position:absolute;left:0;top:1985px;width:1200px;height:530px;background:#fbfcfd}
.blog{position:absolute;left:0;top:2515px;width:1200px;height:405px;background:linear-gradient(100deg,#7fa4cc 0%,#9fbfdc 35%,#6f8c6a 55%,#2f6fa3 80%,#23507f 100%)}
.contact{position:absolute;left:0;top:2920px;width:1200px;height:560px;background:linear-gradient(180deg,#f3f5f8,#e6eaef)}
.site-footer{position:absolute;left:0;top:3480px;width:1200px;height:248px;background:linear-gradient(180deg,#2a2f36,#1b1f24)}
.copyright-bar{position:absolute;left:0;top:3728px;width:1200px;height:69px;background:var(--dark)}

.icon-rail{position:absolute;left:628px;top:818px;width:50px;height:200px;background:var(--white);box-shadow:0 1px 6px rgba(0,0,0,.15);display:flex;flex-direction:column;align-items:center;justify-content:space-around;padding:6px 0}
.icon-rail .item{display:flex;flex-direction:column;align-items:center;font-size:8px;color:var(--muted)}
.dots{position:absolute;left:568px;top:1381px;display:flex;gap:12px}
.dots span{width:12px;height:12px;border-radius:50%;border:1.5px solid #8fa6c4}
.dots span.on{background:#5f7ea6;border-color:#5f7ea6}

.tabs{position:absolute;left:645px;top:1682px;display:flex;gap:4px}
.tabs span{height:34px;padding:0 13px;display:flex;align-items:center;background:var(--tab);font-size:12px;font-weight:600;color:#4a4f55;text-transform:uppercase}
.tabs span.active{background:var(--tab-active);color:#2f4b6e}

.home-card{position:absolute;top:2185px;width:233px;height:235px;background:#e9ebee}
.home-card .cap{position:absolute;left:0;top:170px;width:233px;height:65px;background:#c4c8cd;padding:10px 10px;font-size:12px;font-weight:600;color:var(--ink);line-height:21px}
.home-card .star{position:absolute;right:6px;top:4px;width:16px;height:16px;background:var(--white);display:flex;align-items:center;justify-content:center}

.blog-panel{position:absolute;left:660px;top:220px;width:440px;height:168px;background:rgba(30,40,50,.78);padding:16px 26px;color:var(--white)}
.blog-panel .date{text-align:right;font-size:12px;margin-bottom:6px}
.blog-panel p{font-size:13px;line-height:22px}

.input{position:absolute;height:44px;background:rgba(255,255,255,.85);border:1px solid var(--line);font-size:12px;color:var(--muted);padding:14px 12px}
.submit{position:absolute;left:520px;top:3345px;width:160px;height:45px;background:var(--dark);color:var(--white);font-weight:700;font-size:14px;display:flex;align-items:center;justify-content:center;text-transform:uppercase}

.footer-brand{position:absolute;left:96px;top:100px;display:flex;align-items:center;gap:10px;font-family:"Josefin Sans",sans-serif;font-weight:600;color:var(--white);font-size:24px;letter-spacing:2px}
.footer-brand .mark{width:16px;height:16px;background:var(--white)}
.footer h4,.site-footer h4{font-size:15px;font-weight:700;color:var(--white);text-transform:uppercase;margin-bottom:14px;border-bottom:1px solid rgba(255,255,255,.3);padding-bottom:6px;display:inline-block}
.contact-list{list-style:none;color:#e4e7ea;font-size:11px;line-height:17px}
.contact-list li{display:flex;gap:12px;margin-bottom:12px;align-items:flex-start}
.hours{font-size:11px;color:#e4e7ea;line-height:26px}
.hours div{display:flex}
.hours div span:first-child{width:110px}
.social{position:absolute;right:95px;top:20px;display:flex;gap:12px}
.social span{width:30px;height:30px;border-radius:50%}
</style>
</head>
<body>

<header class="site-header">
  <div class="brand"><span class="mark"></span>HARBORLINE REALTY GROUP</div>
  <nav class="main-nav"><span>Home</span><span>Qeno Info</span><span>About Qe No Home</span><span>Downloads</span><span>Contact Us</span></nav>
</header>

<section class="hero">
  <div class="photo" role="img" aria-label="Mountain lake house with pine forest reflected in clear water" style="inset:0;background:linear-gradient(180deg,rgba(120,160,200,.2),rgba(40,60,50,.35))"></div>
  <h1>FIND YOUR NEW HOME</h1>
  <div class="search-tab">Seach Homes</div>
  <div class="search-bar"><div class="field">Search home by city &amp; state, zip...
    <div class="go"><svg width="20" height="20" viewBox="0 0 20 20"><circle cx="8" cy="8" r="6" fill="none" stroke="#1f1f1f" stroke-width="2.5"/><line x1="12.5" y1="12.5" x2="18" y2="18" stroke="#1f1f1f" stroke-width="3"/></svg></div></div></div>
  <div class="slide-arrow" style="left:14px;top:258px"><svg width="12" height="12" viewBox="0 0 12 12"><path d="M8 1L3 6l5 5" fill="none" stroke="#fff" stroke-width="2"/></svg></div>
  <div class="slide-arrow" style="right:14px;top:258px"><svg width="12" height="12" viewBox="0 0 12 12"><path d="M4 1l5 5-5 5" fill="none" stroke="#fff" stroke-width="2"/></svg></div>
</section>

<section class="properties">
  <h2 class="section-title" style="left:52px;top:100px"><span class="num">01</span>Properties to Select</h2>
  <p class="body abs" style="left:100px;top:186px;width:460px">Lorem Ipsum is simply dummy text of the printing and typesetting industry. Lorem Ipsum has been the industry's standard dummy text ever since the 1500s, when an unknown printer took a galley of type and scrambled it to make a type specimen book. It has survived not only five centuries, but also the leap into electronic typesetting, remaining essentially unchanged. It was popularised in the 1960s with the release of Letraset sheets...</p>
  <div class="btn-outline" style="left:100px;top:366px;width:156px;height:44px">Read More <span class="dot"><svg width="7" height="7" viewBox="0 0 7 7"><path d="M2 1l3 2.5L2 6" fill="none" stroke="#fff" stroke-width="1.4"/></svg></span></div>
  <div class="abs" style="left:712px;top:94px;width:392px;height:285px;border:3px solid var(--frame)"></div>
  <div class="photo" role="img" aria-label="Lakeside family home with wooden dock and deck chairs" style="left:685px;top:126px;width:380px;height:282px;background:linear-gradient(180deg,#5f9ad8 0%,#9fc4e6 30%,#d8c9a8 55%,#6e7b5c 78%,#5a6e7a 100%)"></div>
</section>
<div class="icon-rail">
  <div class="item"><svg width="16" height="16" viewBox="0 0 16 16"><path d="M2 14L14 2M9 2h5v5M2 9v5h5" fill="none" stroke="#3a9b4a" stroke-width="1.8"/></svg>Area</div>
  <div class="item"><svg width="18" height="14" viewBox="0 0 18 14"><rect x="1" y="6" width="16" height="5" fill="#3a9b4a"/><rect x="1" y="2" width="3" height="11" fill="#3a9b4a"/></svg>Beds</div>
  <div class="item"><svg width="18" height="14" viewBox="0 0 18 14"><path d="M1 6h16v3a4 4 0 0 1-4 4H5a4 4 0 0 1-4-4z" fill="#3a9b4a"/><rect x="3" y="1" width="2" height="5" fill="#3a9b4a"/></svg>Bath</div>
  <div class="item"><svg width="18" height="14" viewBox="0 0 18 14"><path d="M3 7l2-5h8l2 5v5H3z" fill="#3a9b4a"/></svg>Garage</div>
</div>
<div class="photo" role="img" aria-label="Tropical villa with palm trees and lawn" style="left:100px;top:1120px;width:315px;height:228px;background:linear-gradient(180deg,#8fb9e0 0%,#cfdbe6 40%,#b9a78a 60%,#5d8a4a 100%)"></div>
<div class="photo" role="img" aria-label="Patio dining table overlooking a mountain lake" style="left:442px;top:1120px;width:315px;height:228px;background:linear-gradient(180deg,#e8e2d6 0%,#8fb6d6 35%,#5b7d5a 60%,#2f3236 100%)"></div>
<div class="photo" role="img" aria-label="Lake house at dusk with fountain and gardens" style="left:785px;top:1120px;width:315px;height:228px;background:linear-gradient(180deg,#2f5a3a 0%,#6a8e4a 40%,#8a5a3a 62%,#3a6a4a 100%)"></div>
<div class="dots"><span></span><span class="on"></span><span></span></div>

<section class="about">
  <h2 class="section-title" style="right:94px;top:112px">About Qe No Home<span class="num">02</span></h2>
  <div class="abs" style="left:65px;top:96px;width:385px;height:260px;border:3px solid var(--frame)"></div>
  <div class="photo" role="img" aria-label="Covered outdoor lounge with sofas and garden view" style="left:95px;top:125px;width:413px;height:280px;background:linear-gradient(160deg,#3d6a5a 0%,#6c8a7a 35%,#c7b8a0 60%,#8a8f94 100%)"></div>
  <div class="tabs" style="top:192px"><span>Room Dimension</span><span class="active">Interior Room</span><span>Exterior Room</span></div>
  <p class="body abs" style="left:565px;top:262px;width:535px">There are many variations of passages of Lorem Ipsum available, but the majority havesuae suffered alteration in some form, by injected humour, or randomised words which don't look even slightly believable. If you are going to use a passage of Lorem Ipsum, There are many variations of passages of Lorem Ipsum available, but the majority have suffered alteration in some form, by injected humour, or randomised words which don't look even.</p>
</section>

<section class="featured">
  <h2 class="section-title" style="left:52px;top:112px"><span class="num">03</span>Featured Homes</h2>
  <p class="body abs" style="left:100px;top:190px;width:245px;text-align:justify">Lorem Ipsum is simply dummy text of the printing and typesetting industry. Lorem Ipsum has been the industry's standard dummy text ever since the 1500s, when an unknown printer took a galley of type and scrambled it to make a type specimen book. It has survived not...</p>
  <div class="btn-outline" style="left:100px;top:390px;width:132px;height:44px">View All <span class="dot"><svg width="7" height="7" viewBox="0 0 7 7"><path d="M2 1l3 2.5L2 6" fill="none" stroke="#fff" stroke-width="1.4"/></svg></span></div>
</section>
<div class="home-card" style="left:372px">
  <div class="photo" role="img" aria-label="Backyard pool surrounded by tall pines" style="left:0;top:0;width:233px;height:170px;background:linear-gradient(180deg,#5f8a4a 0%,#3e5e3a 50%,#4aa0c0 80%,#7a6a5a 100%)"></div>
  <div class="star"><svg width="11" height="11" viewBox="0 0 12 12"><path d="M6 0l1.8 3.8 4.2.5-3.1 2.9.8 4.1L6 9.2 2.3 11.3l.8-4.1L0 4.3l4.2-.5z" fill="#e9b64a"/></svg></div>
  <div class="cap">Luxury Real Estate Home From Midwest, United States</div>
</div>
<div class="home-card" style="left:620px">
  <div class="photo" role="img" aria-label="Infinity pool deck with lounge chairs among evergreens" style="left:0;top:0;width:233px;height:170px;background:linear-gradient(180deg,#7fb0e0 0%,#4a7a4a 45%,#b89a7a 70%,#4aa0d0 100%)"></div>
  <div class="star"><svg width="11" height="11" viewBox="0 0 12 12"><path d="M6 0l1.8 3.8 4.2.5-3.1 2.9.8 4.1L6 9.2 2.3 11.3l.8-4.1L0 4.3l4.2-.5z" fill="#e9b64a"/></svg></div>
  <div class="cap">Luxury Real Estate Home From Midwest, United States</div>
</div>
<div class="home-card" style="left:867px">
  <div class="photo" role="img" aria-label="Log lake house with mountains and blue sky" style="left:0;top:0;width:233px;height:170px;background:linear-gradient(180deg,#3f7fd0 0%,#a9c9ea 35%,#6a8a5a 60%,#2f6a9a 100%)"></div>
  <div class="star"><svg width="11" height="11" viewBox="0 0 12 12"><path d="M6 0l1.8 3.8 4.2.5-3.1 2.9.8 4.1L6 9.2 2.3 11.3l.8-4.1L0 4.3l4.2-.5z" fill="#e9b64a"/></svg></div>
  <div class="cap">Luxury Real Estate Home From Midwest, United States</div>
</div>

<section class="blog">
  <div class="photo" role="img" aria-label="Glass-walled terrace with white armchairs over a pool and lake" style="inset:0;background:linear-gradient(180deg,rgba(255,255,255,.05),rgba(0,0,0,.15))"></div>
  <h2 class="section-title" style="right:42px;top:100px;color:var(--white)">From Blog Post<span class="num" style="color:#d9e3f0">04</span></h2>
  <div class="blog-panel">
    <div class="date">&#9638; 15 Apr 2018</div>
    <p>Nam libero tempore, cum soluta nobis est eligendi optio cumque nihil impedit quo minus id quod maxime placeat facere possimus, omnis voluptas assumenda est, omnis dolor repellendus temporibus autem quibu</p>
  </div>
  <div class="slide-arrow" style="left:14px;top:220px"><svg width="12" height="12" viewBox="0 0 12 12"><path d="M8 1L3 6l5 5" fill="none" stroke="#fff" stroke-width="2"/></svg></div>
  <div class="slide-arrow" style="right:14px;top:220px"><svg width="12" height="12" viewBox="0 0 12 12"><path d="M4 1l5 5-5 5" fill="none" stroke="#fff" stroke-width="2"/></svg></div>
</section>

<section class="contact">
  <h2 class="abs" style="left:0;width:1200px;top:158px;text-align:center;font-family:'Josefin Sans',sans-serif;font-weight:700;font-size:30px;letter-spacing:1px;color:var(--ink)">STAY IN OUR TOUCH!</h2>
  <p class="abs" style="left:0;width:1200px;top:215px;text-align:center;font-size:12px;color:var(--text)">It's on you how you want to a new home. Everyone has a choice. I pick my choice.</p>
</section>
<div class="input" style="left:200px;top:3180px;width:258px">Enter Name</div>
<div class="input" style="left:471px;top:3180px;width:258px">Email Address</div>
<div class="input" style="left:742px;top:3180px;width:258px">Phone</div>
<div class="input" style="left:200px;top:3240px;width:800px;height:70px">Message</div>
<div class="submit">Submit Now</div>

<footer class="site-footer">
  <div class="footer-brand"><span class="mark"></span>HARBORLINE</div>
  <div class="abs" style="left:522px;top:58px;width:300px">
    <h4>Harborline Realty Group</h4>
    <ul class="contact-list">
      <li><svg width="12" height="14" viewBox="0 0 12 14"><path d="M6 0a5 5 0 0 1 5 5c0 4-5 9-5 9S1 9 1 5a5 5 0 0 1 5-5z" fill="#fff"/><circle cx="6" cy="5" r="2" fill="#1f2328"/></svg><span>412 B, Linden Grove Avenue, Suite 140<br>Midwest, United States 5678</span></li>
      <li><svg width="12" height="12" viewBox="0 0 12 12"><path d="M2 0h3l1 3-2 1a7 7 0 0 0 4 4l1-2 3 1v3a1 1 0 0 1-1 1A11 11 0 0 1 1 1a1 1 0 0 1 1-1z" fill="#fff"/></svg><span>Office: (+1) 555 014 2290</span></li>
      <li><svg width="13" height="10" viewBox="0 0 13 10"><rect width="13" height="10" fill="#fff"/><path d="M0 0l6.5 5L13 0" fill="none" stroke="#1f2328" stroke-width="1.2"/></svg><span>hello@harborlinerealty.com</span></li>
    </ul>
  </div>
  <div class="abs" style="left:888px;top:58px;width:220px">
    <h4>Opening Time</h4>
    <div class="hours">
      <div><span>Monday - Friday</span><span>9am to 7:30pm</span></div>
      <div><span>Saturday</span><span>10am to 4:30pm</span></div>
      <div><span>Sunday</span><span>Closed</span></div>
    </div>
  </div>
</footer>
<div class="copyright-bar">
  <p class="abs" style="left:96px;top:26px;font-size:12px;color:#e4e7ea">© Copyright 2018 Harborline Realty Group. All Rights Reserved.</p>
  <div class="social"><span style="background:#2c4f9e"></span><span style="background:#2aa3e0"></span><span style="background:#d6336c"></span><span style="background:#b5347d"></span></div>
</div>

</body>
</html>
```